Heron Property Inspection business card

I am the principal inspector of Heron Property Inspections. I serve Northern Virginia from Winchester to Arlington.Associate, Federated Guild of Dwelling Examiners (FGDE)Graduate, FGDE Home Inspectors CourseNational Association of Home Inspectors ExamI'd like the business card to look more professional than comical.I pulled the attached picture off the web. I'd like to have something like that or an image of a house as my logo on the cards.

Target Market(s)

Persons who recently purchased a home.

Industry/Entity Type

Business

Contact Information for Business Card

Bob AllenBadger Home Inspections, LLC.4455 River RoadBluemont, Virginia 20135cell: 703-231-6680e-mail: tkmarlow@postvale.net

Font styles to use
Serif
Sans Serif

Requirements
Must have
• I'd like to have a logo, something that identifies me as a home inspector. The attached images are something that I'd like to have incorporated into my business card logo.
Nice to have
• I'd like a sketch of a house and/or a magnifying glass showing a house being inspected. The attached images are used as a suggestion only, I do not own the images.
Should not have
• Gimmicky stuff. I want to appear professional and trustworthy.

```html
<!DOCTYPE html>
<html lang="en">
<head>
<meta charset="utf-8">
<title>Heron Property Inspections – Business Card</title>
<link rel="stylesheet" href="https://fonts.googleapis.com/css2?family=Marcellus&family=Exo+2:wght@400;500&display=swap">
<style>
  :root {
    --page-bg: #e6e6e4;
    --card-bg: #eeeeec;
    --card-edge: #d4d4d2;
    --brand-red: #9b1b20;
    --swoosh-dark: #3b3b3e;
    --swoosh-tan: #c9ab8e;
    --ink: #4a4a4c;
    --ink-soft: #55565a;
    --white: #ffffff;
  }
  html, body {
    margin: 0;
    padding: 0;
    width: 1200px;
    height: 902px;
    overflow: hidden;
    background: var(--page-bg);
  }
  .stage {
    position: relative;
    width: 1200px;
    height: 902px;
  }
  .card {
    position: absolute;
    left: 131px;
    top: 183.5px;
    width: 938px;
    height: 535px;
    border-radius: 16px;
    background: var(--card-bg);
    box-shadow: 0 0 0 1px var(--card-edge), 0 14px 34px rgba(0,0,0,0.12);
    overflow: hidden;
    transform: scale(1.12);
    transform-origin: center center;
  }
  .card__corners {
    position: absolute;
    inset: 0;
    width: 938px;
    height: 535px;
  }
  .brand {
    position: absolute;
    right: 68px;
    top: 58px;
    display: flex;
    flex-direction: column;
    align-items: flex-end;
    text-align: right;
    font-family: "Marcellus", serif;
    font-weight: 400;
    color: var(--ink);
    line-height: 1;
  }
  .brand__mark {
    display: block;
    width: 62px;
    height: 62px;
    margin-bottom: 16px;
    background: var(--brand-red);
  }
  .brand__owner {
    display: block;
    font-size: 48px;
    margin-bottom: 14px;
  }
  .brand__company {
    display: block;
    font-size: 36px;
  }
  .person {
    position: absolute;
    left: 38px;
    top: 288px;
  }
  .person__name {
    margin: 0;
    font-family: "Marcellus", serif;
    font-weight: 400;
    font-size: 38px;
    color: var(--brand-red);
    line-height: 1;
  }
  .person__title {
    margin: 6px 0 0;
    font-family: "Exo 2", sans-serif;
    font-size: 23px;
    color: var(--ink-soft);
    line-height: 1;
  }
  .contact {
    position: absolute;
    left: 38px;
    top: 392px;
    margin: 0;
    padding: 0;
    list-style: none;
    font-family: "Exo 2", sans-serif;
    font-weight: 500;
    font-size: 25px;
    color: var(--ink);
  }
  .contact__item {
    display: flex;
    align-items: center;
    height: 36px;
  }
  .contact__icon {
    width: 25px;
    height: 25px;
    margin-right: 18px;
    flex: none;
  }
</style>
</head>
<body>
<main class="stage">
  <article class="card">
    <svg class="card__corners" viewBox="0 0 938 535" aria-hidden="true">
      <g class="corner corner--top-left">
        <path d="M0,236 C24,124 110,34 228,0 L0,0 Z" fill="var(--brand-red)"/>
        <path d="M206,5 C112,42 40,118 10,214 C46,128 114,56 206,5 Z" fill="var(--swoosh-tan)"/>
        <path d="M214,4 C118,40 46,112 14,206 C60,118 126,58 214,4 Z" fill="var(--swoosh-dark)"/>
      </g>
      <g class="corner corner--bottom-right" transform="rotate(180 469 267.5)">
        <path d="M0,236 C24,124 110,34 228,0 L0,0 Z" fill="var(--brand-red)"/>
        <path d="M206,5 C112,42 40,118 10,214 C46,128 114,56 206,5 Z" fill="var(--swoosh-tan)"/>
        <path d="M214,4 C118,40 46,112 14,206 C60,118 126,58 214,4 Z" fill="var(--swoosh-dark)"/>
      </g>
    </svg>

    <div class="brand">
      <span class="brand__mark" aria-hidden="true"></span>
      <span class="brand__owner">Tim Marlow</span>
      <span class="brand__company">Heron Property Inspections, LLC</span>
    </div>

    <div class="person">
      <h1 class="person__name">Employee Name</h1>
      <p class="person__title">Managing Director</p>
    </div>

    <ul class="contact">
      <li class="contact__item">
        <svg class="contact__icon" viewBox="0 0 24 24" aria-hidden="true">
          <rect width="24" height="24" rx="4" fill="var(--brand-red)"/>
          <path d="M7.5 5 L10 7.5 L8.6 9.6 C9.4 11.6 11.4 13.8 13.6 14.9 L15.6 13.4 L18.5 16 L16.8 18.6 C11.4 18.2 5.8 12.6 5.3 7 Z" fill="var(--white)"/>
        </svg>
        <span>703-555-0192</span>
      </li>
      <li class="contact__item">
        <svg class="contact__icon" viewBox="0 0 24 24" aria-hidden="true">
          <rect width="24" height="24" rx="4" fill="var(--brand-red)"/>
          <rect x="4.5" y="7" width="15" height="10.5" fill="none" stroke="var(--white)" stroke-width="1.6"/>
          <path d="M4.8 7.4 L12 13 L19.2 7.4 M4.8 17.2 L10 12 M19.2 17.2 L14 12" fill="none" stroke="var(--white)" stroke-width="1.4"/>
        </svg>
        <span>tkmarlow@postvale.net</span>
      </li>
      <li class="contact__item">
        <svg class="contact__icon" viewBox="0 0 24 24" aria-hidden="true">
          <rect width="24" height="24" rx="4" fill="var(--brand-red)"/>
          <path d="M12 4.5 C8.9 4.5 7 6.8 7 9.4 C7 12.8 12 19 12 19 C12 19 17 12.8 17 9.4 C17 6.8 15.1 4.5 12 4.5 Z" fill="none" stroke="var(--white)" stroke-width="1.6"/>
          <circle cx="12" cy="9.6" r="1.9" fill="var(--white)"/>
        </svg>
        <span>7182 Quarry LaneFernhill, Virginia 20148</span>
      </li>
    </ul>
  </article>
</main>
</body>
</html>
```